Tusk Hollow Lodge website (design only)

Tusk Hollow Lodge (http://www.tuskhollowlodge-mw.example) is a private Safari lodge located in Malawi.
We would like a modern, professional website designed that does not subscribe to the cliched view of a Safari in Africa, but still maintain a wildlife/safari atmosphere.

The aim of our website is to entice people & drive them to the booking form.

Here are some examples of websites that we like. Although we would like our site to be a bit more in line with modern web design trends.

http://www.marulaplains.example/
http://www.kovunde.example/
http://www.tembalorecamp.example/

Requirements
Must have
• Here is a list of the pages required. Most of them will follow a standard content layout. I.e. heading, body and images.

If you take a look at the website, you will get an idea of hoe many page types there are +- 5

http://www.tuskhollowlodge-mw.example/index.htm

About Tusk Hollow
Lirundu Country Club
Rooms
Conferences
Cuisine
Facilities
Your Safari
Activities
Rates & Special Offers
Booking form
Latest Developments
How To Get There
Gallery
Contact Us
Blog / Newsfeed

```html
<!DOCTYPE html>
<html lang="en">
<head>
<meta charset="utf-8">
<title>Tusk Hollow Lodge</title>
<link href="https://fonts.googleapis.com/css2?family=Arimo:ital,wght@0,400;0,700;1,400&display=swap" rel="stylesheet">
<style>
:root{
  --sky-top:#3f86d6; --sky-low:#9cc6ee; --leaf:#3c7a2a; --leaf-dark:#1f4a1a; --grass:#78b83c;
  --panel-light:rgba(220,228,240,.55); --panel-dark:rgba(38,48,66,.86); --panel-deep:rgba(10,14,18,.82);
  --footer:rgba(48,66,84,.82); --nav:#343a44; --nav-text:#e8ecf2; --text:#f2f4f6; --muted:#c9d0d8;
  --accent-red:#e8262a; --cream:#f3efc2; --button-bg:#e8ecef; --button-text:#33404c; --arrow:#2d6fc0;
}
*{margin:0;padding:0;box-sizing:border-box}
html,body{width:1200px;height:1126px;overflow:hidden}
body{position:relative;font-family:"Arimo",Arial,sans-serif;color:var(--text);background:var(--sky-top)}
.abs{position:absolute}
.backdrop{left:0;top:0;width:1200px;height:1126px;background:linear-gradient(180deg,var(--sky-top) 0%,var(--sky-low) 38%,var(--leaf) 52%,var(--leaf-dark) 75%,var(--grass) 100%)}
.brand{left:131px;top:8px;width:217px;height:106px;background:#1e4ca0;border:1px solid #7aa0e0;display:flex;flex-direction:column;align-items:center;justify-content:center;text-align:center;color:#fff}
.brand .name{font-size:24px;line-height:27px}
.brand .estate{font-size:14px;line-height:17px;margin-top:4px}
.main-nav{left:380px;top:8px;width:688px;height:39px;background:var(--nav);display:flex;align-items:center;justify-content:center;font-size:12px;color:var(--nav-text);box-shadow:0 2px 4px rgba(0,0,0,.4);white-space:nowrap}
.main-nav span{padding:0 7px;border-right:1px solid #8b929c;line-height:13px;white-space:nowrap;flex:none}
.main-nav span:last-child{border-right:0}
.dropdown{left:730px;top:47px;width:96px;background:var(--nav);font-size:11px;color:var(--nav-text)}
.dropdown div{padding:4px 5px;border-bottom:1px solid #59606a;white-space:nowrap;line-height:13px}
.dropdown div:last-child{border-bottom:0}
.social{display:flex;gap:6px}
.social i{display:block;width:28px;height:28px;border-radius:5px;background:#5b7393;border:1px solid #c8d4e4}
.call{left:834px;top:62px;font-size:25px;color:#fff;text-shadow:0 1px 2px rgba(0,0,0,.4);white-space:nowrap}
.call b{color:var(--accent-red);font-weight:400}
.panel-light{left:131px;top:132px;width:937px;height:345px;background:var(--panel-light)}
.panel-dark{left:150px;top:151px;width:899px;height:651px;background:var(--panel-dark)}
.panel-lower{left:150px;top:478px;width:899px;height:324px;background:rgba(12,26,20,.55)}
.video{left:169px;top:170px;width:335px;height:239px;background:#111}
.video .frame{position:absolute;left:0;top:10px;width:335px;height:186px;background:linear-gradient(180deg,#8b9a7c 0%,#6fa04a 35%,#5d9a3c 100%)}
.video .bar{position:absolute;left:0;bottom:0;width:335px;height:43px;background:#222;font-size:11px;color:#ddd}
.feature-photo{left:521px;top:170px;width:311px;height:239px;background:linear-gradient(180deg,#8fb9e4 0%,#b59860 55%,#8c7a3e 100%)}
.feature-list{left:832px;top:170px;width:199px}
.feature-list div{height:77px;margin-bottom:4px;background:#2a3544;padding:10px 12px}
.feature-list h3{font-size:13px;font-weight:400;margin-bottom:8px}
.feature-list p{font-size:10px;line-height:16px;color:var(--muted)}
.welcome{left:169px;top:430px;font-size:24px;font-weight:400;white-space:nowrap}
.book{left:675px;top:417px;width:244px;height:49px;background:var(--button-bg);border:1px solid #aab;display:flex;align-items:center;padding-left:13px;font-size:20px;color:var(--button-text);white-space:nowrap}
.book svg{margin-left:10px;flex:none}
.col{top:478px;height:324px}
.col h2{position:absolute;top:30px;left:79px;font-size:21px;font-weight:400;white-space:nowrap}
.col .icon{position:absolute;top:22px;left:29px;width:46px;height:44px;background:#c48a1c;border-radius:3px}
.col p{font-size:11.5px;line-height:18.8px}
.col .more{position:absolute;right:23px;bottom:46px;font-size:12px}
.about{left:150px;width:290px;border-right:1px solid rgba(255,255,255,.2)}
.about p{position:absolute;left:19px;top:85px;width:255px}
.updates{left:440px;width:324px}
.updates .thumb{position:absolute;left:23px;top:87px;width:111px;height:89px;background:linear-gradient(180deg,#7fa36e,#5e8c3e)}
.updates .side{position:absolute;left:145px;top:83px;width:160px}
.updates .full{position:absolute;left:23px;top:195px;width:280px}
.testimonial{left:764px;top:494px;width:267px;height:284px;background:var(--panel-deep)}
.testimonial h2{top:16px;left:70px}
.testimonial .icon{top:8px;left:22px}
.testimonial p{position:absolute;left:19px;top:66px;width:235px;font-style:italic}
.testimonial .more{bottom:30px}
.footer{left:131px;top:820px;width:937px;height:306px;background:var(--footer)}
.quick-title{left:169px;top:836px;font-size:18px;font-weight:400}
.links{top:882px;list-style:none;font-size:11.5px;line-height:23.4px;white-space:nowrap}
.links li::before{content:"";display:inline-block;width:4px;height:4px;border-radius:50%;background:#fff;margin-right:8px;vertical-align:middle}
.footer-name{left:770px;top:868px;width:245px;text-align:center;font-size:28px;line-height:32px;color:var(--cream)}
.contact-title{left:837px;top:950px;font-size:18px;font-weight:400}
.contact{left:837px;top:984px;font-size:11.5px;line-height:20px;font-style:normal;white-space:nowrap}
.rule{left:169px;top:1043px;width:490px;border-top:1px dotted rgba(255,255,255,.5)}
.legal{left:169px;top:1048px;font-size:10px;color:var(--muted);white-space:nowrap}
.legal span{margin-right:33px}
.copy{left:169px;top:1090px;font-size:10px;color:var(--muted);white-space:nowrap}
</style>
</head>
<body>
<div class="abs backdrop" role="img" aria-label="Blue sky with clouds over green trees and lawn"></div>

<header>
  <div class="abs brand"><div class="name">Tusk Hollow<br>Lodge</div><div class="estate">Mlambe Estate<br>Khonde</div></div>
  <nav class="abs main-nav">
    <span>About Tusk Hollow</span><span>Rooms</span><span>Conferences</span><span>Cuisine</span><span>Facilities</span><span>Your Safari</span><span>Gallery</span><span>Activities</span><span>Contact US</span><span>Blog</span>
  </nav>
  <div class="abs dropdown"><div>Rates &amp; Offers</div><div>Booking Reqst</div><div>Special Offers</div><div>How to get reach</div></div>
  <div class="abs social" style="left:379px;top:66px" aria-label="Social links"><i></i><i></i><i></i><i></i></div>
  <div class="abs call"><b>Call on</b> - 555-20-7316</div>
</header>

<div class="abs panel-light"></div>
<div class="abs panel-dark"></div>
<div class="abs panel-lower"></div>

<section>
  <div class="abs video">
    <div class="frame" role="img" aria-label="Video still of a golfer on a green course"></div>
    <svg class="abs" style="left:142px;top:90px" width="50" height="34"><rect width="50" height="34" rx="5" fill="#222" opacity=".85"/><path d="M20 9 L33 17 L20 25Z" fill="#fff"/></svg>
    <div class="bar">
      <svg class="abs" style="left:0;top:4px" width="335" height="36"><rect x="0" y="0" width="335" height="5" fill="#555"/><circle cx="8" cy="3" r="5" fill="#ddd"/><path d="M22 15 L32 21 L22 27Z" fill="#ddd"/><path d="M62 18 h4 l5 -4 v14 l-5 -4 h-4z" fill="#ddd"/><circle cx="239" cy="21" r="5" fill="none" stroke="#ddd" stroke-width="1.5"/><path d="M300 14 h4 M300 14 v4 M316 14 h-4 M316 14 v4 M300 28 h4 M300 28 v-4 M316 28 h-4 M316 28 v-4" stroke="#ddd" stroke-width="1.5"/></svg>
      <span class="abs" style="left:94px;top:19px">0:00 / 0:41</span>
    </div>
  </div>
  <div class="abs feature-photo" role="img" aria-label="Giraffes beside a tree in tall grass"></div>
  <div class="abs feature-list">
    <div><h3>Lodge Booking</h3><p>Lorem Ipsum is simply of the printing and typesetting industry.</p></div>
    <div><h3>VIP Membership</h3><p>Lorem Ipsum is simply of the printing and typesetting industry.</p></div>
    <div><h3>Meet the Experts</h3><p>Lorem Ipsum is simply of the printing and typesetting industry.</p></div>
  </div>
  <h1 class="abs welcome">Welcome to Tusk Hollow Lodge...</h1>
  <div class="abs book">Online Booking
    <svg width="80" height="24"><path d="M0 3 H66 L78 12 L66 21 H0Z" fill="var(--arrow)"/><text x="7" y="16" font-size="11" fill="#fff" font-family="Arimo,Arial,sans-serif">Click Here</text></svg>
  </div>
</section>

<section>
  <div class="abs col about">
    <div class="icon" role="img" aria-label="Giraffe emblem"></div>
    <h2>About Us</h2>
    <p>Lorem Ipsum is simply dummy text of the printing and typesetting industry. Lorem Ipsum has been the industry's standard dummy text ever since the 1500s, when an unknown printer took a galley of type and scrambled it to make a type specimen book.<br>Lorem Ipsum is simply dummy text of the printing and typesetting industry.</p>
    <span class="more">Read more...</span>
  </div>
  <div class="abs col updates">
    <div class="icon" role="img" aria-label="Giraffe emblem"></div>
    <h2>Tusk Hollow Updates</h2>
    <div class="thumb" role="img" aria-label="Zebra grazing on grass"></div>
    <p class="side">Lorem Ipsum is simply dummy text of the printing and typesetting industry.with the release of Letraset sheets containing Lorem Ipsum.</p>
    <p class="full">Lorem Ipsum is simply dummy text of the printing and typesetting industry.Lorem Ipsum is simply dummy text of the printing and typesetting industry.</p>
    <span class="more">Read more...</span>
  </div>
  <div class="abs col testimonial">
    <div class="icon" role="img" aria-label="Giraffe emblem"></div>
    <h2>Testimonial</h2>
    <p>Lorem Ipsum is simply dummy text of the printing and typesetting industry.Lorem Ipsum is simply dummy text of the printing and type-setting industry.Lorem Ipsum is simply dummy text of the printing and typesetting industry.Lorem Ipsum is simply dummy text of the printing and typesetting industry.Lorem Ipsum is simply dummy text of the printing and typesetting industry.</p>
    <span class="more">Read more...</span>
  </div>
</section>

<footer>
  <div class="abs footer"></div>
  <h2 class="abs quick-title">QUICK LINKS</h2>
  <ul class="abs links" style="left:189px"><li>Events 123 lorem</li><li>456 Events ipsum</li><li>852 Events</li><li>Events 789</li><li>Events 632</li><li>Events745</li></ul>
  <ul class="abs links" style="left:348px"><li>Events 123 lorem</li><li>456 Events ipsum</li><li>852 Events</li><li>Events 789</li><li>Events 632 lorem ipsum</li><li>Events745</li></ul>
  <ul class="abs links" style="left:543px"><li>Events 123 lorem</li><li>456 Events ipsum</li><li>852 Events</li><li>Events 789</li></ul>
  <div class="abs footer-name">Tusk Hollow<br>Lodge</div>
  <h2 class="abs contact-title">CONTACT</h2>
  <address class="abs contact">12/7c, Kapiri Ridge Road<br>Sample Country-4412093<br>T: 05512340-7716</address>
  <div class="abs rule"></div>
  <div class="abs legal"><span>Terms &amp; Conditions</span><span>Privacy</span><span>Sitemap</span></div>
  <div class="abs social" style="left:666px;top:1029px" aria-label="Social links"><i></i><i></i><i></i><i></i></div>
  <div class="abs copy">The official website of Tusk Hollow Lodge.Copyright © 2011.</div>
</footer>
</body>
</html>
```